Business Card & Stationary
Powder Coating Company
Project: Business Card & Stationary
Business Card & Stationary - Miscellaneous
Creative Brief
Professional
Laurent Bexhold
Owner / Operator
4172 Ave K 1/2
nullemail@tarrowfinishline.com
www.tarrowfinishline.com
Should list our services, which include Powder Coating, Ceramic Coating and Abrasive Blasting

```html
<!DOCTYPE html>
<html lang="en">
<head>
<meta charset="utf-8">
<title>Tarrow Finish Line – Business Cards</title>
<link rel="stylesheet" href="https://fonts.googleapis.com/css2?family=Source+Sans+3:wght@400;700&display=swap">
<style>
  :root {
    --red: #c4111b;
    --red-dark: #8e0a10;
    --ink: #2a2a2a;
    --white: #ffffff;
    --black: #000000;
    --border: #9a9a9a;
    --page: #ffffff;
  }
  * { box-sizing: border-box; margin: 0; padding: 0; }
  html, body {
    width: 1200px; height: 713px; overflow: hidden;
    background: var(--page);
    font-family: "Source Sans 3", "Myriad Pro", Arial, sans-serif;
  }
  .sheet { position: relative; width: 1200px; height: 713px; }
  .card {
    position: absolute; width: 574px; height: 326px; overflow: hidden;
  }
  .card--front { left: 14px; top: 17px; background: var(--white); border: 1px solid var(--border); }
  .card--red   { left: 612px; top: 17px; background: var(--red); }
  .card--white { left: 14px; top: 372px; background: var(--white); border: 1px solid var(--border); }
  .card--black { left: 612px; top: 372px; background: var(--black); }

  .wave { position: absolute; inset: 0; width: 100%; height: 100%; }

  .brand {
    display: flex; align-items: center; gap: 10px;
    font-weight: 700; font-size: 34px; line-height: 1; letter-spacing: 0.5px;
  }
  .brand__dot { width: 16px; height: 16px; border-radius: 50%; flex: none; }

  .card--front .brand { position: absolute; left: 24px; top: 40px; font-size: 30px; color: var(--red); }
  .card--front .brand__dot { background: var(--red); }

  .person { position: absolute; left: 272px; top: 92px; color: var(--ink); }
  .person__name { font-size: 22px; font-weight: 400; color: var(--red-dark); }
  .person__role { font-size: 15px; margin-top: 4px; }

  .contact {
    position: absolute; left: 24px; top: 222px;
    list-style: none; color: var(--white); font-size: 14px; line-height: 17px;
  }

  .back {
    position: absolute; inset: 0;
    display: flex; flex-direction: column; align-items: center;
  }
  .back .brand { margin-top: 112px; }
  .back .services {
    margin-top: 76px; text-align: center; font-size: 16px; line-height: 22px;
  }
  .card--red .brand, .card--red .services { color: var(--white); }
  .card--red .brand__dot { background: var(--white); }
  .card--white .brand { color: var(--red); }
  .card--white .brand__dot { background: var(--red); }
  .card--white .services { color: var(--ink); }
  .card--black .brand, .card--black .services { color: var(--white); }
  .card--black .brand__dot { background: var(--red); }
</style>
</head>
<body>
<main class="sheet">

  <section class="card card--front">
    <svg class="wave" viewBox="0 0 574 326" preserveAspectRatio="none" aria-hidden="true">
      <path d="M0,196 C170,222 380,206 574,52 L574,326 L0,326 Z" fill="#8e0a10"/>
      <path d="M0,204 C170,230 385,214 574,64 L574,326 L0,326 Z" fill="#c4111b"/>
    </svg>
    <div class="brand"><span class="brand__dot"></span>Tarrow Finish Line</div>
    <div class="person">
      <p class="person__name">Laurent Bexhold</p>
      <p class="person__role">Owner / Operator</p>
    </div>
    <ul class="contact">
      <li>4172 Ave K 1/2</li>
      <li>Phone: (312) 555-4706</li>
      <li>Fax: (312) 555-4719</li>
      <li>Email: nullemail@tarrowfinishline.com</li>
      <li>www.tarrowfinishline.com</li>
    </ul>
  </section>

  <section class="card card--red">
    <div class="back">
      <div class="brand"><span class="brand__dot"></span>Tarrow Finish Line</div>
      <p class="services">which include Powder Coating,<br>Ceramic Coating and Abrasive Blasting</p>
    </div>
  </section>

  <section class="card card--white">
    <div class="back">
      <div class="brand"><span class="brand__dot"></span>Tarrow Finish Line</div>
      <p class="services">which include Powder Coating,<br>Ceramic Coating and Abrasive Blasting</p>
    </div>
  </section>

  <section class="card card--black">
    <div class="back">
      <div class="brand"><span class="brand__dot"></span>Tarrow Finish Line</div>
      <p class="services">which include Powder Coating,<br>Ceramic Coating and Abrasive Blasting</p>
    </div>
  </section>

</main>
</body>
</html>
```